Veltrane Group Business Card Design

The CEO is looking for a new trendy look for his business card.
You can stay with current branding or come up with something new/creative. It can be 3D, including Medical Office buildings. You can use our logo in a variety of colors. Please include name, title, company name, company website, email address, cell number

Target Market(s)

Real Estate Development and Construction

Industry/Entity Type

Health care real estate

Contact Information for Business Card

Rohesh Kamdar, CEO M-604.781.2249 E-roheshkamdar@veltrane.com Address:4180 Lindqvist Ave, Tampa, FL 33482 www.veltrane.com

Font styles to use
Other font styles liked:
• Be creative

Requirements
Must have
• Creative, trendy look
Nice to have
• Please go to our website to get a feel- www. veltrane.com
Should not have
• small fonts

```html
<!DOCTYPE html>
<html lang="en">
<head>
<meta charset="utf-8">
<title>Veltrane Group Business Card</title>
<link href="https://fonts.googleapis.com/css2?family=Arimo:wght@400;700&display=swap" rel="stylesheet">
<style>
  :root {
    --stage: #3a3a3a;
    --brand-red: #b0202b;
    --brand-pink: #e0566a;
    --navy: #1c2a4a;
    --white: #ffffff;
    --card-w: 525px;
    --card-h: 300px;
  }
  * { box-sizing: border-box; margin: 0; padding: 0; }
  html, body {
    width: 1200px; height: 689px; overflow: hidden;
    background: var(--stage);
    font-family: "Arimo", Arial, sans-serif;
  }
  .stage {
    position: relative; width: 1200px; height: 689px;
    display: flex; align-items: center; justify-content: center; gap: 50px;
  }
  .card {
    position: relative; width: var(--card-w); height: var(--card-h);
    border-radius: 18px; overflow: hidden;
  }
  .card--front {
    background: var(--brand-red);
    display: flex; flex-direction: column; align-items: center; justify-content: center;
  }
  .front__wordmark {
    color: var(--brand-pink); font-weight: 700; font-size: 50px; letter-spacing: -1px;
    margin-top: -10px;
  }
  .front__web {
    position: absolute; bottom: 46px; left: 0; right: 0; text-align: center;
    color: var(--white); font-size: 13px; letter-spacing: 3.5px;
  }
  .card--back { background: var(--white); }
  .back__band { position: absolute; inset: 0; }
  .back__name {
    position: absolute; top: 22px; right: 34px; text-align: right;
  }
  .back__person { color: var(--brand-red); font-weight: 700; font-size: 23px; }
  .back__title { color: var(--navy); font-size: 12px; margin-top: 2px; }
  .back__wordmark {
    position: absolute; left: 34px; top: 108px;
    color: var(--brand-red); font-weight: 700; font-size: 40px; letter-spacing: -1px;
  }
  .back__contact {
    position: absolute; right: 22px; bottom: 22px; text-align: right;
    color: var(--white); font-size: 12.5px; line-height: 1.4;
  }
  .contact__address { margin-bottom: 8px; }
  .contact__row { display: flex; align-items: center; justify-content: flex-end; gap: 7px; }
  .contact__icon { width: 12px; height: 12px; flex: none; }
</style>
</head>
<body>
<main class="stage">
  <section class="card card--front">
    <div class="front__wordmark">Veltrane Group</div>
    <div class="front__web">www.veltrane.com</div>
  </section>

  <section class="card card--back">
    <svg class="back__band" viewBox="0 0 525 300" preserveAspectRatio="none" aria-hidden="true">
      <polyline points="0,262 170,266 525,60" fill="none" stroke="var(--navy)" stroke-width="5"/>
      <polygon points="0,274 174,278 525,72 525,300 0,300" fill="var(--brand-red)"/>
    </svg>
    <div class="back__name">
      <div class="back__person">Rohesh Kamdar</div>
      <div class="back__title">CEO</div>
    </div>
    <div class="back__wordmark">Veltrane Group</div>
    <div class="back__contact">
      <div class="contact__address">4180 Lindqvist Ave, Tampa<br>FL 33482</div>
      <div class="contact__row">604.781.2249
        <svg class="contact__icon" viewBox="0 0 12 12" aria-hidden="true"><path d="M2.5 1 L4.5 1 L5.2 3.5 L4 4.5 Q5 7 7.5 8 L8.5 6.8 L11 7.5 L11 9.5 Q10.5 11 9 11 Q1 10 1 2.5 Q1 1 2.5 1Z" fill="var(--white)"/></svg>
      </div>
      <div class="contact__row">roheshkamdar@veltrane.com
        <svg class="contact__icon" viewBox="0 0 12 12" aria-hidden="true"><rect x="1" y="2.5" width="10" height="7" fill="var(--white)"/><polyline points="1,2.5 6,6.5 11,2.5" fill="none" stroke="var(--brand-red)" stroke-width="1"/></svg>
      </div>
      <div class="contact__row">www.veltrane.com
        <svg class="contact__icon" viewBox="0 0 12 12" aria-hidden="true"><circle cx="6" cy="6" r="5" fill="var(--white)"/><ellipse cx="6" cy="6" rx="2" ry="5" fill="none" stroke="var(--brand-red)" stroke-width="0.8"/><line x1="1" y1="6" x2="11" y2="6" stroke="var(--brand-red)" stroke-width="0.8"/></svg>
      </div>
    </div>
  </section>
</main>
</body>
</html>
```